Web Design Project

We are looking for a new site design for the VELTO Canada. The current site can be found at
http://www.veltocanada-example.org/
The URL is provided for reference. We want a completely different look and layout which is shown in the specifications document.
As part of the design, we want a home page, and inside page.
The design you provide will be implemented in Joomla. The design winner will only need to provide the PSD. We anticipate creating the template coding in-house.
However, if you have experience creating Joomla templates, please let us know as we may ask you to bid separately to do that phase of the project.
We've provided a specifications document which includes wireframes of the home page, and inside page. We've also included a logo file.
For the header at the top, as indicated in the specs document, we want to keep the same overall treatment to every page. We want a graphic treatment with the logo for the header area. In this manner, the design will be flexiable and can be used for future years.
For the home page, we've indicated that we'd like to have a slider implemented within the design.
The wireframe is provided to illustrate the placement of content and menu items. The exact dimensions of each component can be revised as you see fit. We are also flexiable if you feel we have missed items.

```html
<!DOCTYPE html>
<html lang="en">
<head>
<meta charset="utf-8">
<title>VELTO Canada — Home</title>
<link rel="stylesheet" href="https://fonts.googleapis.com/css2?family=PT+Sans:wght@400;700&family=PT+Sans+Narrow:wght@700&family=Open+Sans:wght@400;600&display=swap">
<style>
:root{
  --page-bg:#ececec;
  --white:#ffffff;
  --brand-blue:#1c4a9a;
  --top-line:#1d4b9b;
  --red:#d9161c;
  --red-light:#ec3a3e;
  --red-dark:#b80f14;
  --orange:#f08a1c;
  --orange-light:#f8ac4c;
  --orange-link:#e8520e;
  --link-red:#e0161b;
  --text:#555555;
  --heading:#2a2a2a;
  --border:#d8d8d8;
  --slide-fill:#a8c98c;
  --slide-dots:#56692e;
}
*{box-sizing:border-box;margin:0;padding:0}
html,body{width:1200px;height:1167px;overflow:hidden}
body{background:var(--page-bg);font-family:"Open Sans",sans-serif;color:var(--text);position:relative}
a{text-decoration:none;color:inherit}
.top-line{position:absolute;left:0;top:0;width:1200px;height:3px;background:var(--top-line)}
.page{position:absolute;left:22px;top:3px;width:1149px;height:1164px;background:var(--white)}
.abs{position:absolute}

/* header */
.brand{left:40px;top:24px;display:flex;align-items:center;gap:10px}
.brand-dot{width:30px;height:30px;border-radius:50%;background:var(--red)}
.brand-name{font-family:"PT Sans",sans-serif;font-weight:700;font-size:24px;color:var(--brand-blue);line-height:1.1}
.utility-nav{right:24px;top:15px;font-family:"PT Sans",sans-serif;font-size:14px;color:#444;display:flex}
.utility-nav a{padding:0 13px;border-left:1px solid #777;line-height:14px}
.utility-nav a:first-child{border-left:0}
.utility-nav a:last-child{padding-right:0}
.search{left:866px;top:76px;width:270px;height:33px;border:1px solid var(--border);border-radius:4px;box-shadow:inset 0 1px 3px rgba(0,0,0,.08);font-family:"PT Sans",sans-serif;font-size:13px;color:#888;padding:8px 14px}
.search svg{position:absolute;right:8px;top:7px}

/* main nav */
.main-nav{left:17px;top:132px;width:1125px;height:47px;background:linear-gradient(var(--red-light),var(--red) 55%,var(--red-dark));border-radius:2px;display:flex}
.main-nav a{font-family:"PT Sans",sans-serif;font-weight:700;font-size:18px;color:#fff;line-height:47px;text-align:center;border-right:1px solid rgba(255,255,255,.35)}

/* slider */
.slider{left:18px;top:182px;width:1123px;height:283px;background:var(--slide-fill)}
.slide-caption{left:33px;top:110px;width:368px;height:150px;background:rgba(255,255,255,.88);border-radius:4px;padding:20px 28px}
.slide-title{font-family:"PT Sans Narrow",sans-serif;font-weight:700;font-size:25px;color:var(--red);line-height:1.1}
.slide-sub{font-family:"PT Sans",sans-serif;font-weight:700;font-size:18px;color:var(--brand-blue);margin-top:3px}
.slide-text{font-family:"PT Sans",sans-serif;font-size:14px;color:#2f62b4;line-height:1.4;margin-top:10px}
.slide-dots{left:516px;top:255px;width:91px;height:28px;background:var(--slide-dots);border-radius:6px 6px 0 0;display:flex;justify-content:center;align-items:center;gap:5px}
.slide-dots span{width:9px;height:9px;border-radius:50%;background:#fff}

/* side boxes */
.box{border:1px solid var(--border);background:#fff}
.box-head{height:41px;padding-left:28px;font-family:"PT Sans",sans-serif;font-size:19px;line-height:41px;color:#fff;background:linear-gradient(#2a5bab,var(--brand-blue))}
.box-head.light{background:linear-gradient(#fafafa,#e9e9e9);color:#333;border-bottom:1px solid var(--border)}
.sponsors{left:17px;top:477px;width:276px;height:146px}
.sponsor-logos{display:flex;gap:18px;padding:20px 0 0 27px;font-weight:600;font-size:14px;color:var(--brand-blue)}
.become{display:inline-block;margin:14px 0 0 29px;font-size:14px;color:var(--link-red)}
.login{left:17px;top:636px;width:276px;height:183px}
.field{width:222px;height:31px;margin-left:20px;border:1px solid var(--border);border-radius:4px;font-size:13px;color:#888;padding:6px 11px}
.field:first-of-type{margin-top:13px}
.field+.field{margin-top:9px}
.btn-login{margin:9px 0 0 22px;width:71px;height:31px;border-radius:4px;background:linear-gradient(var(--red-light),var(--red-dark));color:#fff;font-family:"PT Sans",sans-serif;font-weight:700;font-size:15px;text-align:center;line-height:29px;border:1px solid #a80e12}
.connected{left:15px;top:838px;width:277px;height:113px}
.social{display:flex;gap:12px;padding:13px 0 0 20px}
.social span{width:27px;height:27px;border-radius:3px}

/* welcome */
.welcome{left:314px;top:485px;width:534px}
.welcome h1{font-family:"PT Sans",sans-serif;font-weight:400;font-size:25px;color:var(--heading);margin-bottom:10px}
.welcome p{font-size:13px;line-height:22.5px;color:#666;margin-left:3px;margin-bottom:11px}

/* news */
.news{left:862px;top:477px;width:276px;height:316px;border:1px solid var(--border)}
.news-head{height:48px;background:linear-gradient(var(--red-light),var(--red-dark));color:#fff;font-family:"PT Sans",sans-serif;font-size:22px;line-height:48px;padding-left:24px}
.news-item{margin:0 13px 0 24px;padding:17px 0 12px}
.news-item+.news-item{border-top:1px dotted #999}
.news-date{font-size:13px;font-weight:600;color:#333}
.news-text{font-size:12px;color:#666;line-height:20px;margin-top:6px}
.news-more{font-size:12px;font-weight:600;color:var(--red-dark);margin-top:3px;display:block}

/* regions */
.regions{left:317px;top:807px;width:823px;height:244px;border:1px solid var(--border)}
.regions-head{height:44px;background:linear-gradient(#fafafa,#ececec);font-family:"PT Sans",sans-serif;font-size:22px;color:#222;line-height:44px;padding-left:26px}
.region{top:56px;width:185px;height:176px;border:1px solid var(--border);border-radius:4px;overflow:hidden}
.region-head{height:43px;background:linear-gradient(var(--orange-light),var(--orange));color:#fff;font-family:"PT Sans",sans-serif;font-weight:700;font-size:17px;line-height:43px;padding-left:25px}
.region ul{list-style:none;padding:12px 0 0 25px}
.region li{font-size:13px;color:var(--orange-link);line-height:28px}

/* footer */
.footer-line{left:23px;top:1077px;width:1122px;height:1px;background:var(--border)}
.footer-nav{left:0;top:1092px;width:1149px;display:flex;justify-content:center;font-family:"PT Sans",sans-serif;font-size:15px;color:#444}
.footer-nav a{padding:0 15px;border-left:1px solid #666;line-height:15px}
.footer-nav a:first-child{border-left:0}
.copyright{left:0;top:1130px;width:1149px;text-align:center;font-size:11px;color:#444}
</style>
</head>
<body>
<div class="top-line"></div>
<div class="page">

  <header>
    <a class="abs brand" href="#"><span class="brand-dot"></span><span class="brand-name">VELTO<br>Canada</span></a>
    <nav class="abs utility-nav"><a href="#">Home</a><a href="#">Contact Us</a><a href="#">VELTO International</a></nav>
    <div class="abs search">Search here..
      <svg width="20" height="20" viewBox="0 0 20 20"><circle cx="8" cy="8" r="6" fill="none" stroke="#888" stroke-width="2.2"/><line x1="12.5" y1="12.5" x2="18" y2="18" stroke="#888" stroke-width="2.6" stroke-linecap="round"/></svg>
    </div>
    <nav class="abs main-nav">
      <a href="#" style="width:114px">About</a>
      <a href="#" style="width:93px">Board</a>
      <a href="#" style="width:118px">Chapters</a>
      <a href="#" style="width:165px">Member Space</a>
      <a href="#" style="width:229px">Resources &amp; Knowledge</a>
      <a href="#" style="width:146px">Sponsorship</a>
      <a href="#" style="width:105px;border-right:0">Exhibit</a>
    </nav>
  </header>

  <section class="abs slider" role="img" aria-label="Slider photo: green vineyard fields under a blue sky">
    <div class="abs slide-caption">
      <div class="slide-title">VELTO INTERNATION PUCH LINE</div>
      <div class="slide-sub">Duis tincidunt lectus quis viverra</div>
      <div class="slide-text">Sed odio est, auctor ac, sollicitudin in, consequat vitae, orci. Fusce id felis.</div>
    </div>
    <div class="abs slide-dots"><span></span><span></span><span></span></div>
  </section>

  <aside>
    <div class="abs box sponsors">
      <div class="box-head">Sponsors</div>
      <div class="sponsor-logos"><span>Northline</span><span>Castwave</span><span>Lumora</span></div>
      <a class="become" href="#">Become a Sponsors <svg width="6" height="9" viewBox="0 0 6 9"><path d="M0 0L6 4.5L0 9Z" fill="#e0161b"/></svg></a>
    </div>
    <div class="abs box login">
      <div class="box-head">Member Login</div>
      <div class="field">Username</div>
      <div class="field">Password</div>
      <div class="btn-login">Login</div>
    </div>
    <div class="abs box connected">
      <div class="box-head light">Stay Connected</div>
      <div class="social">
        <span style="background:#2f4f8f"></span><span style="background:#1c76b0"></span><span style="background:#f07a1a"></span><span style="background:#c7242a"></span>
      </div>
    </div>
  </aside>

  <main class="abs welcome">
    <h1>Welcome to Velto Website Mainpage..</h1>
    <p>Pellentesque habitant morbi tristique senectus et netus et malesuada fames ac turpis egestas. In posuere felis nec tortor. Pellentesque faucibus. Ut accumsan ultricies elit. Maecenas at justo id velit placerat molestie.</p>
    <p>Donec dictum lectus non odio. Cras a ante vitae enim iaculis aliquam. Mauris nunc quam, venenatis nec, euismod sit amet, egestas placerat, est. Pellentesque habitant morbi tristique senectus et netus et malesuada fames ac turpis egestas. Cras id elit. Integer quis urna. Ut ante enim, dapibus Mauris vel lacus vitae felis vestibulum volutpat. Etiam est nunc, venenatis in, tristique eu, imperdiet ac, nisl.</p>
    <p>Cum sociis natoque penatibus et magnis dis parturient montes, nascetur ridiculus mus. In iaculis facilisis massa. Etiam eu urna.</p>
  </main>

  <section class="abs news">
    <div class="news-head">News &amp; Events</div>
    <div class="news-item">
      <div class="news-date">20 Nov 2012</div>
      <div class="news-text">Do you need to convince your employer of the value that your membership and participation.</div>
      <a class="news-more" href="#">Learn More</a>
    </div>
    <div class="news-item">
      <div class="news-date">18 Dec 2012</div>
      <div class="news-text">Lorem ipsum dolor sit amet, consectetuer adipiscing elit. Nam cursus</div>
      <a class="news-more" href="#">Learn More</a>
    </div>
  </section>

  <section class="abs regions">
    <div class="regions-head">Regions</div>
    <div class="abs region" style="left:15px">
      <div class="region-head">Mountain Pacific</div>
      <ul><li>Vancouver Island</li><li>Vancouver</li><li>Calgary</li></ul>
    </div>
    <div class="abs region" style="left:213px">
      <div class="region-head">Western</div>
      <ul><li>Edmonton</li><li>Saskatchewan</li><li>Winnipeg</li></ul>
    </div>
    <div class="abs region" style="left:411px">
      <div class="region-head">Central</div>
      <ul><li>National Capital-Ottawa</li><li>Southwestern Ontario</li><li>Montreal</li><li>Toronto</li></ul>
    </div>
    <div class="abs region" style="left:610px">
      <div class="region-head">Atlantic</div>
      <ul><li>Nova Scotia</li><li>Terra-Nova, St. John's</li><li>Prince Edward Island</li><li>Atlantic, St. John's</li></ul>
    </div>
  </section>

  <footer>
    <div class="abs footer-line"></div>
    <nav class="abs footer-nav">
      <a href="#">Home</a><a href="#">About</a><a href="#">Board</a><a href="#">Chapters</a><a href="#">Member Space</a><a href="#">Resources &amp; Knowledge</a><a href="#">Sponsorship</a><a href="#">Exhibit</a><a href="#">Member Login</a><a href="#">Contact Us</a>
    </nav>
    <div class="abs copyright">Privacy Policy &nbsp;|&nbsp; Copyright © &nbsp;2013 Company Name. &nbsp;All right reserved</div>
  </footer>

</div>
</body>
</html>
```